Sable Grove products by Voldrin. Beauty, skin care cosmetic products

We are an all natural and organic beauty product company looking for a logo an label design ideas. Our motto is to make products that are safe, natural, in harmony with the earth and that really work. Our products will contribute to the transition from the Old Earth to the Sable Grove (as the image of the two worlds suggests). The earths can be mixed in the label. The label example is a rough sketch.
Updates

The label needs to be 1 (one) inch high and 7 inch long.

Need extra days to review

Target Market(s)

Products made with natural and organic ingredients. Beauty and skin products

Requirements
Must have
• My project must be standing out. We want customers to be draw to he product on the shelf. Wow, this label is different? what is it? All natural? I must try it.
• Must be bold but not outrageous.
• The two earth can be placed on right and left side of the tree of life on the second attachment
Nice to have
• The two Earth can be in the back ground suggesting that this product takes us from chemically and artificially filled products to something new that is in harmony with nature and health.
Should not have
• Should not be boring. Ordinary, easy to forget and ignore patterns, lettering, logos.

```html
<!DOCTYPE html>
<html lang="en">
<head>
<meta charset="utf-8">
<title>Sable Grove Under-Arm-Balm Labels</title>
<link rel="stylesheet" href="https://fonts.googleapis.com/css2?family=Sorts+Mill+Goudy&family=Marcellus&family=Montserrat:wght@700;800&display=swap">
<style>
:root{
  --stage:#231f20;
  --ink:#ffffff;
  --leaf:#7dc242;
  --deep:#0a1228;
  --blue:#2347b0;
  --sky:#2f66d6;
  --paper:#ffffff;
  --badge:#c9252c;
}
*{box-sizing:border-box;margin:0;padding:0}
html,body{width:1200px;height:992px;overflow:hidden;background:var(--stage)}
.sheet{position:relative;width:1200px;height:992px}
.label{position:absolute;left:101px;width:998px;height:143px;overflow:hidden;color:var(--ink);border:1px solid #3a6ad0}
.label:nth-child(1){top:101px}
.label:nth-child(2){top:263px}
.label:nth-child(3){top:425px}
.label:nth-child(4){top:586px}
.label:nth-child(5){top:748px}
.backdrop{position:absolute;inset:0;
  background:
    radial-gradient(ellipse 150px 110px at 499px 72px, rgba(8,14,30,.95) 0%, rgba(10,20,45,.9) 70%, rgba(10,20,45,0) 100%),
    linear-gradient(90deg,#2448b4 0%,#1d3580 18%,#0f1c40 32%,#0a1228 42%,#0b1430 60%,#1a3a9a 70%,#2452c4 85%,#2a5fd2 100%);}
.details{position:absolute;left:21px;top:14px;width:280px;font-family:"Sorts Mill Goudy",serif;font-size:8.4px;line-height:11px}
.details p{margin-bottom:4px}
.details b{font-weight:700}
.warning{position:absolute;left:15px;top:102px;width:271px;height:30px;border:1px solid var(--ink);padding:3px 6px;font-family:"Sorts Mill Goudy",serif;font-size:8.4px;line-height:11px}
.scent{position:absolute;left:320px;top:71px;transform:translate(-50%,-50%) rotate(-90deg);white-space:nowrap;font-family:"Marcellus",serif;font-size:15px;color:var(--leaf)}
.title{position:absolute;left:499px;top:14px;transform:translateX(-50%);text-align:center;white-space:nowrap}
.brand{font-family:"Marcellus",serif;font-size:19.5px;line-height:22px}
.maker{font-family:"Marcellus",serif;font-size:12px;line-height:20px}
.maker b{font-family:"Montserrat",sans-serif;font-weight:800;font-size:17px;letter-spacing:.3px}
.product{font-family:"Montserrat",sans-serif;font-weight:800;font-size:20px;color:var(--leaf);margin-top:9px;letter-spacing:.5px}
.claim{font-family:"Marcellus",serif;font-size:11px;margin-top:10px;letter-spacing:.3px}
.free{font-family:"Montserrat",sans-serif;font-size:10px;font-weight:400;margin-top:3px}
.free b{font-weight:700}
.info{position:absolute;left:714px;top:25px;font-family:"Sorts Mill Goudy",serif;font-size:9.5px;line-height:12px}
.info .site{position:absolute;top:32px;white-space:nowrap}
.info .site span{font-family:"Marcellus",serif;font-size:12.5px}
.bestby{position:absolute;left:714px;top:97px;width:101px;height:15px;background:var(--paper);color:#333;font-family:"Sorts Mill Goudy",serif;font-size:9.5px;padding:1px 5px}
.weight{position:absolute;left:714px;top:121px;font-family:"Sorts Mill Goudy",serif;font-size:9.5px;white-space:nowrap}
.origin{position:absolute;left:831px;top:98px;width:34px;height:34px;border-radius:50%;background:var(--badge);border:2px solid var(--paper)}
.marks{position:absolute;left:883px;top:8px;width:30px}
.marks svg{display:block}
.socials{position:absolute;left:882px;top:101px;display:grid;grid-template-columns:14px 14px;gap:4px}
.socials i{display:block;width:14px;height:14px;border-radius:50%;background:var(--paper)}
.sticker{position:absolute;left:925px;top:9px;width:61px;height:125px;background:var(--paper)}
</style>
</head>
<body>
<main class="sheet">

<section class="label">
  <div class="backdrop" role="img" aria-label="Artwork of two earths flanking a tree of life in deep blues"></div>
  <div class="details">
    <p><b>INGREDIENTS:</b> Organic Coconut (Cocos Nucifera) Oil, Organic Bees Wax, West African Shea (Butyrospermum Parkii) Butter, Arrowroot (Manihot Esculenta) Powder, Magnesium Oil, Nahcolite (Natural Baking Soda)</p>
    <p><b>DIRECTIONS:</b> Using the tip of your finger or a spatula apply a pea size of balm to each underarm. Stinging may occur after shave. Wait a few minutes and then apply.</p>
  </div>
  <div class="warning"><b>WARNING:</b> External use only. Discontinue use if irritation occurs. Do not apply to open cuts or wounds.</div>
  <div class="scent">Original Scent</div>
  <div class="title">
    <div class="brand">Sable Grove Products</div>
    <div class="maker">by <b>VOLDRIN</b></div>
    <div class="product">UNDER-ARM-BALM</div>
    <div class="claim">100% NATURAL INGREDIENTS</div>
    <div class="free"><b>No</b> Aluminum, <b>No</b> Parabens, <b>No</b> Phthalates</div>
  </div>
  <div class="info">Manufactured by Voldrin<br>Linden Vale MD 20977<div class="site">Learn more at: <span>VOLDRIN.COM</span></div></div>
  <div class="bestby">Best by</div>
  <div class="weight">Net Wt. 2oz (56 g)</div>
  <div class="origin"></div>
  <div class="marks"><svg width="30" height="88" viewBox="0 0 30 88"><rect x="3" y="4" width="24" height="20" rx="3" fill="none" stroke="#fff" stroke-width="1.5"/><polygon points="15,30 26,50 4,50" fill="none" stroke="#7dc242" stroke-width="2"/><circle cx="15" cy="72" r="9" fill="none" stroke="#fff" stroke-width="1.5"/></svg></div>
  <div class="socials"><i></i><i></i><i></i><i></i></div>
  <div class="sticker"></div>
</section>

<section class="label">
  <div class="backdrop" role="img" aria-label="Artwork of two earths flanking a tree of life in deep blues"></div>
  <div class="details">
    <p><b>INGREDIENTS:</b> Organic Coconut (Cocos Nucifera) Oil, Organic Bees Wax, West African Shea (Butyrospermum Parkii) Butter, Arrowroot (Manihot Esculenta) Powder, Magnesium Oil, Nahcolite (Natural Baking Soda), White Fir (Abies Concolor) Essential Oil.</p>
    <p><b>DIRECTIONS:</b> Using the tip of your finger or a spatula apply a pea size of balm to each underarm. Stinging may occur after shave. Wait a few minutes and then apply.</p>
  </div>
  <div class="warning"><b>WARNING:</b> External use only. Discontinue use if irritation occurs. Do not apply to open cuts or wounds.</div>
  <div class="scent">White Fir</div>
  <div class="title">
    <div class="brand">Sable Grove Products</div>
    <div class="maker">by <b>VOLDRIN</b></div>
    <div class="product">UNDER-ARM-BALM</div>
    <div class="claim">100% NATURAL INGREDIENTS</div>
    <div class="free"><b>No</b> Aluminum, <b>No</b> Parabens, <b>No</b> Phthalates</div>
  </div>
  <div class="info">Manufactured by Voldrin<br>Linden Vale MD 20977<div class="site">Learn more at: <span>VOLDRIN.COM</span></div></div>
  <div class="bestby">Best by</div>
  <div class="weight">Net Wt. 2oz (56 g)</div>
  <div class="origin"></div>
  <div class="marks"><svg width="30" height="88" viewBox="0 0 30 88"><rect x="3" y="4" width="24" height="20" rx="3" fill="none" stroke="#fff" stroke-width="1.5"/><polygon points="15,30 26,50 4,50" fill="none" stroke="#7dc242" stroke-width="2"/><circle cx="15" cy="72" r="9" fill="none" stroke="#fff" stroke-width="1.5"/></svg></div>
  <div class="socials"><i></i><i></i><i></i><i></i></div>
  <div class="sticker"></div>
</section>

<section class="label">
  <div class="backdrop" role="img" aria-label="Artwork of two earths flanking a tree of life in deep blues"></div>
  <div class="details">
    <p><b>INGREDIENTS:</b> Organic Coconut (Cocos Nucifera) Oil, Organic Bees Wax, West African Shea (Butyrospermum Parkii) Butter, Arrowroot (Manihot Esculenta) Powder, Magnesium Oil, Nahcolite (Natural Baking Soda), Lemongrass (Cymbopogon Citratus) Essential Oil</p>
    <p><b>DIRECTIONS:</b> Using the tip of your finger or a spatula apply a pea size of balm to each underarm. Stinging may occur after shave. Wait a few minutes and then apply.</p>
  </div>
  <div class="warning"><b>WARNING:</b> External use only. Discontinue use if irritation occurs. Do not apply to open cuts or wounds.</div>
  <div class="scent">Lemongrass</div>
  <div class="title">
    <div class="brand">Sable Grove Products</div>
    <div class="maker">by <b>VOLDRIN</b></div>
    <div class="product">UNDER-ARM-BALM</div>
    <div class="claim">100% NATURAL INGREDIENTS</div>
    <div class="free"><b>No</b> Aluminum, <b>No</b> Parabens, <b>No</b> Phthalates</div>
  </div>
  <div class="info">Manufactured by Voldrin<br>Linden Vale MD 20977<div class="site">Learn more at: <span>VOLDRIN.COM</span></div></div>
  <div class="bestby">Best by</div>
  <div class="weight">Net Wt. 2oz (56 g)</div>
  <div class="origin"></div>
  <div class="marks"><svg width="30" height="88" viewBox="0 0 30 88"><rect x="3" y="4" width="24" height="20" rx="3" fill="none" stroke="#fff" stroke-width="1.5"/><polygon points="15,30 26,50 4,50" fill="none" stroke="#7dc242" stroke-width="2"/><circle cx="15" cy="72" r="9" fill="none" stroke="#fff" stroke-width="1.5"/></svg></div>
  <div class="socials"><i></i><i></i><i></i><i></i></div>
  <div class="sticker"></div>
</section>

<section class="label">
  <div class="backdrop" role="img" aria-label="Artwork of two earths flanking a tree of life in deep blues"></div>
  <div class="details">
    <p><b>INGREDIENTS:</b> Organic Coconut (Cocos Nucifera) Oil, Organic Bees Wax, West African Shea (Butyrospermum Parkii) Butter, Arrowroot (Manihot Esculenta) Powder, Magnesium Oil, Nahcolite (Natural Baking Soda), Fressia (Fressia Corymbosa) Essential Oil</p>
    <p><b>DIRECTIONS:</b> Using the tip of your finger or a spatula apply a pea size of balm to each underarm. Stinging may occur after shave. Wait a few minutes and then apply.</p>
  </div>
  <div class="warning"><b>WARNING:</b> External use only. Discontinue use if irritation occurs. Do not apply to open cuts or wounds.</div>
  <div class="scent">Fressia</div>
  <div class="title">
    <div class="brand">Sable Grove Products</div>
    <div class="maker">by <b>VOLDRIN</b></div>
    <div class="product">UNDER-ARM-BALM</div>
    <div class="claim">100% NATURAL INGREDIENTS</div>
    <div class="free"><b>No</b> Aluminum, <b>No</b> Parabens, <b>No</b> Phthalates</div>
  </div>
  <div class="info">Manufactured by Voldrin<br>Linden Vale MD 20977<div class="site">Learn more at: <span>VOLDRIN.COM</span></div></div>
  <div class="bestby">Best by</div>
  <div class="weight">Net Wt. 2oz (56 g)</div>
  <div class="origin"></div>
  <div class="marks"><svg width="30" height="88" viewBox="0 0 30 88"><rect x="3" y="4" width="24" height="20" rx="3" fill="none" stroke="#fff" stroke-width="1.5"/><polygon points="15,30 26,50 4,50" fill="none" stroke="#7dc242" stroke-width="2"/><circle cx="15" cy="72" r="9" fill="none" stroke="#fff" stroke-width="1.5"/></svg></div>
  <div class="socials"><i></i><i></i><i></i><i></i></div>
  <div class="sticker"></div>
</section>

<section class="label">
  <div class="backdrop" role="img" aria-label="Artwork of two earths flanking a tree of life in deep blues"></div>
  <div class="details">
    <p><b>INGREDIENTS:</b> Organic Coconut (Cocos Nucifera) Oil, Organic Bees Wax, West African Shea (Butyrospermum Parkii) Butter, Arrowroot (Manihot Esculenta) Powder, Magnesium Oil, Nahcolite (Natural Baking Soda), Lilac (Syringa Vulgaris) Essential Oil</p>
    <p><b>DIRECTIONS:</b> Using the tip of your finger or a spatula apply a pea size of balm to each underarm. Stinging may occur after shave. Wait a few minutes and then apply.</p>
  </div>
  <div class="warning"><b>WARNING:</b> External use only. Discontinue use if irritation occurs. Do not apply to open cuts or wounds.</div>
  <div class="scent">Lilac</div>
  <div class="title">
    <div class="brand">Sable Grove Products</div>
    <div class="maker">by <b>VOLDRIN</b></div>
    <div class="product">UNDER-ARM-BALM</div>
    <div class="claim">100% NATURAL INGREDIENTS</div>
    <div class="free"><b>No</b> Aluminum, <b>No</b> Parabens, <b>No</b> Phthalates</div>
  </div>
  <div class="info">Manufactured by Voldrin<br>Linden Vale MD 20977<div class="site">Learn more at: <span>VOLDRIN.COM</span></div></div>
  <div class="bestby">Best by</div>
  <div class="weight">Net Wt. 2oz (56 g)</div>
  <div class="origin"></div>
  <div class="marks"><svg width="30" height="88" viewBox="0 0 30 88"><rect x="3" y="4" width="24" height="20" rx="3" fill="none" stroke="#fff" stroke-width="1.5"/><polygon points="15,30 26,50 4,50" fill="none" stroke="#7dc242" stroke-width="2"/><circle cx="15" cy="72" r="9" fill="none" stroke="#fff" stroke-width="1.5"/></svg></div>
  <div class="socials"><i></i><i></i><i></i><i></i></div>
  <div class="sticker"></div>
</section>

</main>
</body>
</html>
```